ULMIRA card Technical Architecture

Hello everyone ULMIRA: It is a consulting firm in Architecture and Construction. I require a card duplexing, sober, elegant, classic but not boring. Update 1: Use the following data for the card. Name: Gonzalo Pereda Mauricio Villalta Position: COO Twitter: @ulmiraAT Homepage: ulmira-example.com home address not include the participation of all thank you.

Target Market(s)

Construction companies, Architects and Consulting Engineers

Industry/Entity Type

Consulting

Contact Information for Business Card

Los campos que debe tener:
Nombre, Cargo, email, homepage y twitter

Font styles to use
Serif
Sans Serif
Other font styles liked:
• Me gustan playfair display, open sans y roboto, pero estoy sujeto a sus propuestas

Requirements
Must have
• Colors: Present combined proposals in white, red, gray and black Update 1: The two names must be clearly differentiated from the two surnames
Nice to have
• They are free to present their best proposals. I will bring them immediate feedback to the extent you can go see their designs. Complete data for card and logo files will give the winner the

```html
<!DOCTYPE html>
<html lang="en">
<head>
<meta charset="utf-8">
<title>ULMIRA – Business Card</title>
<link href="https://fonts.googleapis.com/css2?family=Playfair+Display:wght@400;700&family=Roboto:wght@300;400&display=swap" rel="stylesheet">
<style>
  :root{
    --bg:#e9e6e1;
    --red-light:#d8333f;
    --red:#c3202c;
    --red-dark:#9e1620;
    --white:#ffffff;
    --white-soft:rgba(255,255,255,.85);
    --black:#0d0d0d;
    --shadow:rgba(0,0,0,.28);
  }
  *{margin:0;padding:0;box-sizing:border-box}
  html,body{width:1200px;height:902px;overflow:hidden;background:var(--bg)}
  .canvas{position:relative;width:1200px;height:902px}
  .card{
    position:absolute;left:290px;width:620px;height:354px;
    background:radial-gradient(ellipse at 40% 35%,var(--red-light) 0%,var(--red) 55%,var(--red-dark) 100%);
    box-shadow:0 10px 26px var(--shadow);
    color:var(--white);overflow:hidden;
  }
  .card--front{top:62px}
  .card--back{top:486px}

  .brand{position:absolute;display:flex;flex-direction:column;align-items:center;font-family:"Roboto",sans-serif}
  .brand__name{display:flex;align-items:center;gap:14px;font-weight:300;letter-spacing:.32em;line-height:1}
  .brand__dot{width:10px;height:10px;border-radius:50%;background:var(--white)}
  .brand__rule{height:1px;background:rgba(255,255,255,.7);margin:8px 0 6px}
  .brand__tagline{font-weight:400;letter-spacing:.3em;text-transform:uppercase}

  .card--front .brand{left:0;right:0;top:138px}
  .card--front .brand__name{font-size:46px}
  .card--front .brand__rule{width:300px}
  .card--front .brand__tagline{font-size:12px}

  .card--back .brand{left:20px;width:320px;top:120px}
  .card--back .brand__name{font-size:38px}
  .card--back .brand__rule{width:260px}
  .card--back .brand__tagline{font-size:10.5px}

  .divider{position:absolute;left:352px;top:26px;width:1px;height:240px;background:var(--white-soft)}

  .person{position:absolute;left:372px;top:26px;width:230px}
  .person__name{font-family:"Playfair Display",serif;font-size:21px;line-height:27px;font-weight:400}
  .person__surname{font-weight:700}
  .person__role{margin-top:6px;font-family:"Roboto",sans-serif;font-size:12px;font-weight:400;letter-spacing:.25em;color:var(--white-soft)}

  .contacts{position:absolute;left:372px;top:150px;list-style:none;font-family:"Roboto",sans-serif;font-size:15px;line-height:24px}
  .contacts li{display:flex;align-items:center;gap:8px}
  .contacts svg{width:12px;height:12px;flex:none}

  .base-band{position:absolute;left:0;right:0;bottom:0;height:62px;background:var(--black)}
</style>
</head>
<body>
<main class="canvas">

  <section class="card card--front" aria-label="Card front">
    <div class="brand">
      <div class="brand__name"><span class="brand__dot"></span>ULMIRA</div>
      <div class="brand__rule"></div>
      <div class="brand__tagline">Arquitectura Técnica</div>
    </div>
  </section>

  <section class="card card--back" aria-label="Card back">
    <div class="brand">
      <div class="brand__name"><span class="brand__dot"></span>ULMIRA</div>
      <div class="brand__rule"></div>
      <div class="brand__tagline">Arquitectura Técnica</div>
    </div>

    <div class="divider"></div>

    <div class="person">
      <p class="person__name">Gonzalo <span class="person__surname">Pereda</span></p>
      <p class="person__name">Mauricio <span class="person__surname">Villalta</span></p>
      <p class="person__role">COO</p>
    </div>

    <ul class="contacts">
      <li>
        <svg viewBox="0 0 12 12" aria-hidden="true"><rect width="12" height="12" rx="2" fill="#fff"/><path d="M3.5 2.5l1.5 0 .6 2-1 .7a5 5 0 0 0 2.2 2.2l.7-1 2 .6v1.5c-3.5.3-6.3-2.5-6-6z" fill="#c3202c"/></svg>
        0400 118 362
      </li>
      <li>
        <svg viewBox="0 0 12 12" aria-hidden="true"><rect width="12" height="12" rx="2" fill="#fff"/><rect x="2.5" y="3.5" width="7" height="5" fill="none" stroke="#c3202c" stroke-width="1"/><path d="M2.5 3.5l3.5 3 3.5-3" fill="none" stroke="#c3202c" stroke-width="1"/></svg>
        info@ulmira-example.com
      </li>
      <li>
        <svg viewBox="0 0 12 12" aria-hidden="true"><rect width="12" height="12" rx="2" fill="#fff"/><circle cx="6" cy="6" r="3.2" fill="none" stroke="#c3202c" stroke-width="1"/><path d="M2.8 6h6.4M6 2.8v6.4" stroke="#c3202c" stroke-width=".8"/></svg>
        www.ulmira-example.com
      </li>
      <li>
        <svg viewBox="0 0 12 12" aria-hidden="true"><rect width="12" height="12" rx="2" fill="#fff"/><circle cx="6" cy="6" r="2.6" fill="#c3202c"/></svg>
        @ulmiraAT
      </li>
    </ul>

    <div class="base-band"></div>
  </section>

</main>
</body>
</html>
```